RESIDENTIAL CONSTRUCTION

We are a company that specializes in building custom residential homes, the design should also emphasize that quality and service is our priority.

Industry/Entity Type

Construction Company

Contact Information for Business Card

Contact Person: Marcus Lindqvist
Company Address: 273 West Alder Ave San Jose , Ca 95380
Phone Number : 408-731-2946
Email Address: Stoneridgehomes517@mailvista.net

Font styles to use
Sans Serif

Colors
ec1f27

Requirements
Must have
• CSLB # 7362015
Nice to have
• needs to have same color as logo i uploaded, we will be printing these on a clear plastic card.

```html
<!DOCTYPE html>
<html lang="en">
<head>
<meta charset="utf-8">
<title>Stoneridge General Builders – Business Card</title>
<link rel="stylesheet" href="https://fonts.googleapis.com/css2?family=Roboto:wght@400;700&display=swap">
<style>
  :root {
    --backdrop: #e4e4e2;
    --card: #f7f7f5;
    --brand-red: #a8202c;
    --ink: #3a3a3a;
  }
  html, body {
    margin: 0;
    padding: 0;
    width: 1200px;
    height: 802px;
    overflow: hidden;
    background: var(--backdrop);
  }
  .canvas {
    position: relative;
    width: 1200px;
    height: 802px;
  }
  .business-card {
    position: absolute;
    left: 100px;
    top: 115px;
    width: 1000px;
    height: 572px;
    background: var(--card);
    box-shadow: 0 8px 28px rgba(0, 0, 0, 0.18);
    font-family: "Roboto", Arial, sans-serif;
  }
  .brand {
    position: absolute;
    left: 80px;
    top: 196px;
    display: flex;
    align-items: center;
    gap: 16px;
  }
  .brand-square {
    width: 58px;
    height: 58px;
    background: var(--brand-red);
    flex: none;
  }
  .brand-name {
    margin: 0;
    font-size: 30px;
    line-height: 1.12;
    font-weight: 700;
    color: var(--brand-red);
    letter-spacing: 0.5px;
  }
  .contact {
    position: absolute;
    left: 560px;
    top: 170px;
    color: var(--ink);
    font-size: 21px;
    line-height: 1.32;
  }
  .contact-name {
    margin: 0 0 12px;
    font-size: 27px;
    font-weight: 700;
    letter-spacing: 1.5px;
    color: var(--brand-red);
    text-transform: uppercase;
  }
  .contact p {
    margin: 0;
  }
  .contact .group {
    margin-bottom: 12px;
  }
</style>
</head>
<body>
<main class="canvas">
  <section class="business-card">
    <div class="brand">
      <div class="brand-square" aria-hidden="true"></div>
      <p class="brand-name">Stoneridge<br>General Builders</p>
    </div>
    <div class="contact">
      <h1 class="contact-name">Marcus Lindqvist</h1>
      <div class="group">
        <p>273 West Alder Ave San Jose</p>
        <p>Ca 95380</p>
        <p>CSLB # 7362015</p>
      </div>
      <p>408-731-2946</p>
      <p>Stoneridgehomes517@mailvista.net</p>
      <p>www.stoneridgebuilders.net</p>
    </div>
  </section>
</main>
</body>
</html>
```